Yacht, Boats, Watersports company needs a redesign of business card

Hello Designers!
We are a Boat dealership company that sells fun in the water, we sell boats, Yachts, Kayaks and also yacht WaterSport toys. We are looking to redesign our business cards in to something a little bit more sophisticated. in a way that we can make better use of our company colors. I'm attaching a zipped file containing the company 3 sets of company logo which one is an horizontal another one is a vertical and also a chromed 3d logo. Also is included two set of business cards that we use and also some designs that i think it's interesting. We use PMS 2026c Orange and PMS 7687C Blue. I would like to see at least two different options with the orange as accent and also using blue as an accent color. It's really important for the business cards to have a font option and size that is legible to most people. Our current website is wwww.coralpennant.com. Please visit if you want to have a better feeling of the Boat dealership
You can send Single sided or double side options. We are now using single sided but we may be open for a double side option if we really like the design.
Target Market(s)
Marine, boat sales, yacht sales, water toys sales/
Contact Information for Business Card
Name: Dale Whitcombe
Address: 212 North Fenwick Lane,
Keel Harbor, FL 33090
Phone: 954-731-8842
Fax: 954:731-8843
Cell: 954-382-1490
Email: dw@coralpennant.com
Website: coralpennant.com
Requirements
Must have
- the current information of the business card provided.
logo
use the PMS Colors
Nice to have
- a touch of elegance and sophistication but simple
Should not have
- should not have any typography that is hard to read, the card should be simple but yet sophisticated.

```html
<!DOCTYPE html>
<html lang="en">
<head>
<meta charset="utf-8">
<title>Coral Pennant Business Card</title>
<link rel="stylesheet" href="https://fonts.googleapis.com/css2?family=Michroma&family=Arimo:wght@400;700&display=swap">
<style>
  :root {
    --orange: #f05a28;
    --blue: #1b4f8f;
    --card: #0c0c0c;
    --ink: #f2f2f2;
    --rule: #5a5a5a;
    --backdrop: #2a2522;
  }
  * { box-sizing: border-box; margin: 0; padding: 0; }
  html, body { width: 1200px; height: 842px; overflow: hidden; }
  body {
    background: var(--backdrop);
    position: relative;
    font-family: "Arimo", Arial, sans-serif;
  }
  .card {
    position: absolute;
    top: 266px;
    width: 540px;
    height: 309px;
    background: var(--card);
    overflow: hidden;
    box-shadow: 0 10px 30px rgba(0,0,0,.55);
  }
  .card--front { left: 40px; }
  .card--back { left: 620px; }

  .band {
    position: absolute;
    left: 0; right: 0;
    height: 14px;
    background: var(--blue);
  }
  .band--top { top: 0; }
  .band--bottom { bottom: 0; }

  .contact {
    position: absolute;
    left: 0; right: 0;
    top: 56px;
    text-align: center;
    color: var(--ink);
  }
  .contact__name {
    font-family: "Michroma", sans-serif;
    font-weight: 400;
    font-size: 19px;
    letter-spacing: 1px;
    text-transform: uppercase;
  }
  .contact__first { color: var(--blue); }
  .contact__last { color: var(--orange); }
  .rule {
    width: 200px;
    height: 1px;
    background: var(--rule);
    margin: 9px auto 8px;
  }
  .contact__lines {
    font-size: 14px;
    line-height: 18px;
  }
  .label { color: var(--orange); font-weight: 700; }
  .accent { color: var(--orange); }
  .contact__address {
    font-size: 15px;
    line-height: 20px;
  }

  .tab {
    position: absolute;
    width: 44px;
    height: 60px;
    background: var(--blue);
  }
  .tab::after {
    content: "";
    position: absolute;
    top: 0; bottom: 0;
    width: 3px;
    background: var(--orange);
  }
  .tab--left { left: 0; top: 124px; }
  .tab--left::after { right: 0; }
  .tab--right { right: 0; top: 22px; }
  .tab--right::after { left: 0; }

  .brand {
    position: absolute;
    left: 0; right: 0;
    top: 100px;
    text-align: center;
  }
  .brand__mark { display: block; margin: 0 auto 18px; }
  .brand__name {
    font-family: "Michroma", sans-serif;
    font-size: 24px;
    letter-spacing: 2px;
    color: var(--orange);
    text-transform: uppercase;
  }
</style>
</head>
<body>
  <section class="card card--front" aria-label="Business card front">
    <div class="band band--top"></div>
    <div class="contact">
      <h1 class="contact__name"><span class="contact__first">Dale</span> <span class="contact__last">Whitcombe</span></h1>
      <div class="rule"></div>
      <p class="contact__lines">
        <span class="label">P:</span> 954-731-8842<br>
        <span class="label">F:</span> 954:731-8843<br>
        <span class="label">M:</span> 954-382-1490<br>
        <span class="label">P:</span> dw@coralpennant.com<br>
        www.<span class="accent">coralpennant</span>.com
      </p>
      <div class="rule"></div>
      <p class="contact__address">212 North Fenwick Lane<br>Keel Harbor, FL 33090</p>
    </div>
    <div class="band band--bottom"></div>
  </section>

  <section class="card card--back" aria-label="Business card back">
    <div class="tab tab--right"></div>
    <div class="tab tab--left"></div>
    <div class="brand">
      <svg class="brand__mark" width="56" height="56" viewBox="0 0 56 56" aria-hidden="true">
        <circle cx="28" cy="28" r="24" fill="none" stroke="var(--orange)" stroke-width="5"/>
      </svg>
      <p class="brand__name">Coral Pennant</p>
    </div>
  </section>
</body>
</html>
```